Design the Business card for NetVaultic

Business card required for a professional Cyber Security business.
Company Logo and Icon has already been provided however I would like other options for the logo and icon to compare to. Alternatively, please refine/enhance the image of the logo.icon I have already provided.

If you are going to use the provided logo and icon, I was thinking that the company raised Logo on White background would serve well on the front of the card. See attached. AND, a large company raised stand-alone icon to appear on black background on the back of the card with tagline 'Cyber Risk Management, Governance and Consulting' or 'Cyber Security for your Business' See attached.
Alternatively, provide your own design for the logo and icon.

Target Market(s)

Enterprise, Government, Financial.

Contact Information for Business Card

Tavin Orloweth
Founder and CEO

Email Address
Mobile Number
Website URL
LinkedIn URL

Logo Text

NetVaultic - see attached example of logo

Font styles to use
Other font styles liked:
• Berlin Sans FB

Requirements
Must have
• Clean large and bold icon on the back with tagline.
• Horizontal alignment,
Nice to have
• Round edges.
• Raised Logo/Icon
Should not have
• An unprofessional look and feel.

```html
<!DOCTYPE html>
<html lang="en">
<head>
<meta charset="UTF-8">
<title>NetVaultic Business Card</title>
<link rel="stylesheet" href="https://fonts.googleapis.com/css2?family=Questrial&family=Roboto:wght@400;500&display=swap">
<style>
  :root {
    --backdrop: #3a3430;
    --card: #1d2126;
    --card-edge: #15181c;
    --silver: #8d9299;
    --blue: #2f7fd6;
    --blue-soft: #4a6fb8;
    --gold: #f0b323;
    --white: #f2f4f7;
    --divider: #4a5058;
  }
  * { box-sizing: border-box; margin: 0; padding: 0; }
  html, body { width: 1200px; height: 769px; overflow: hidden; }
  body {
    background: var(--backdrop);
    position: relative;
    font-family: "Roboto", sans-serif;
  }
  .card {
    position: absolute;
    width: 520px;
    height: 297px;
    background: var(--card);
    border-radius: 10px;
    box-shadow: 0 12px 30px rgba(0,0,0,0.45);
  }
  .card--front { left: 70px; top: 90px; }
  .card--back { left: 610px; top: 380px; }

  .front__brand {
    position: absolute;
    left: 0; right: 0; top: 92px;
    display: flex; align-items: center; justify-content: center; gap: 16px;
  }
  .brand-dot {
    width: 58px; height: 58px; border-radius: 50%;
    background: #2a2f35;
  }
  .front__name {
    font-family: "Questrial", sans-serif;
    font-size: 52px;
    color: var(--silver);
    letter-spacing: 0.5px;
  }
  .front__tagline {
    position: absolute;
    left: 0; right: 0; bottom: 62px;
    text-align: center;
    font-family: "Questrial", sans-serif;
    font-size: 17px;
  }
  .tagline--blue { color: var(--blue-soft); }
  .tagline--gold { color: var(--gold); }

  .back__brand {
    position: absolute;
    left: 36px; top: 0; bottom: 0; width: 190px;
    display: flex; flex-direction: column; align-items: center; justify-content: center; gap: 14px;
  }
  .back__brand .brand-dot {
    width: 110px; height: 110px; background: var(--blue);
  }
  .back__brand-name {
    font-family: "Roboto", sans-serif;
    font-weight: 500;
    font-size: 20px;
    color: var(--white);
  }
  .back__divider {
    position: absolute;
    left: 250px; top: 50px; bottom: 50px;
    width: 1px; background: var(--divider);
  }
  .back__details {
    position: absolute;
    left: 276px; top: 74px;
  }
  .person__name {
    font-weight: 500; font-size: 21px; color: var(--blue);
    text-transform: uppercase;
  }
  .person__title {
    font-weight: 500; font-size: 16px; color: var(--gold);
    text-transform: uppercase; margin-top: 2px; margin-bottom: 16px;
  }
  .contact { list-style: none; }
  .contact__item {
    display: flex; align-items: center; gap: 10px;
    font-size: 16px; color: var(--white); line-height: 24px;
  }
  .contact__icon { width: 14px; height: 14px; flex: none; }
</style>
</head>
<body>
  <section class="card card--front">
    <div class="front__brand">
      <span class="brand-dot"></span>
      <span class="front__name">NetVaultic</span>
    </div>
    <p class="front__tagline">
      <span class="tagline--blue">Cyber Risk Management,</span>
      <span class="tagline--gold">Governance &amp; Consulting</span>
    </p>
  </section>

  <section class="card card--back">
    <div class="back__brand">
      <span class="brand-dot"></span>
      <span class="back__brand-name">NetVaultic</span>
    </div>
    <div class="back__divider"></div>
    <div class="back__details">
      <p class="person__name">Tavin Orloweth</p>
      <p class="person__title">Founder &amp; CEO</p>
      <ul class="contact">
        <li class="contact__item">
          <svg class="contact__icon" viewBox="0 0 14 14"><rect x="3" y="0.5" width="8" height="13" rx="1.5" fill="none" stroke="#2f7fd6" stroke-width="1.5"/><rect x="6" y="10.5" width="2" height="1.2" fill="#2f7fd6"/></svg>
          555 014 2738
        </li>
        <li class="contact__item">
          <svg class="contact__icon" viewBox="0 0 14 14"><rect x="0.5" y="2.5" width="13" height="9" rx="1" fill="#2f7fd6"/><path d="M1 3l6 5 6-5" fill="none" stroke="#1d2126" stroke-width="1.2"/></svg>
          tavin@netvaultic.com
        </li>
        <li class="contact__item">
          <svg class="contact__icon" viewBox="0 0 14 14"><circle cx="7" cy="7" r="6.3" fill="none" stroke="#2f7fd6" stroke-width="1.4"/><ellipse cx="7" cy="7" rx="2.6" ry="6.3" fill="none" stroke="#2f7fd6" stroke-width="1.2"/><line x1="0.7" y1="7" x2="13.3" y2="7" stroke="#2f7fd6" stroke-width="1.2"/></svg>
          www.netvaultic.com
        </li>
        <li class="contact__item">
          <svg class="contact__icon" viewBox="0 0 14 14"><circle cx="7" cy="7" r="6.5" fill="#2f7fd6"/></svg>
          netvaultic
        </li>
      </ul>
    </div>
  </section>
</body>
</html>
```